All-Natural Head Lice Removal company

I need a business card with my pre-existing logo. We are a new company located in Portland Oregon that goes into peoples homes to help with head lice removal. My products and approach are all- natural and also will be around children.On my current logo we used Teal Bl and the color Green. I am open to new ideas just want it simple and creative

Target Market(s)

my biggest market is families of school aged children

Industry/Entity Type

Business

Contact Information for Business Card

see upload for details from previous business card

Font styles to use
Serif

Colors
33a6d7
9bcb3b
f37122

Requirements
Must have
• Basic information/ logo put into a creative format that is catching to the eye
Nice to have
• creative

```html
<!DOCTYPE html>
<html lang="en">
<head>
<meta charset="UTF-8">
<title>ClearNest Business Card</title>
<link href="https://fonts.googleapis.com/css2?family=Comic+Neue:wght@400;700&display=swap" rel="stylesheet">
<style>
  :root {
    --backdrop: #dcd8d2;
    --card: #f3f3f1;
    --card-edge: #d7d7d3;
    --leaf-green: #5fae2e;
    --leaf-green-light: #8cc63f;
    --arc-dark: #1f3219;
    --teal-blue: #2a7db8;
    --ink: #222222;
    --paper-text: #f4f7ef;
  }
  html, body {
    margin: 0;
    padding: 0;
    width: 1200px;
    height: 969px;
    overflow: hidden;
    background: var(--backdrop);
    font-family: "Comic Neue", "Comic Sans MS", sans-serif;
  }
  .canvas {
    position: relative;
    width: 1200px;
    height: 969px;
  }
  .business-card {
    position: absolute;
    left: 100px;
    top: 200px;
    width: 1000px;
    height: 569px;
    border-radius: 34px;
    background: var(--card);
    box-shadow: 0 0 0 1px var(--card-edge), 0 18px 40px rgba(0,0,0,0.18);
    overflow: hidden;
  }
  .card-shapes {
    position: absolute;
    inset: 0;
  }
  .contact-block {
    position: absolute;
    left: 52px;
    top: 302px;
    color: var(--paper-text);
  }
  .contact-name {
    margin: 0;
    font-size: 36px;
    font-weight: 700;
    letter-spacing: 0.5px;
  }
  .contact-role {
    margin: 2px 0 26px;
    font-size: 27px;
  }
  .contact-list {
    list-style: none;
    margin: 0;
    padding: 0;
    font-size: 26px;
  }
  .contact-list li {
    display: flex;
    align-items: center;
    gap: 12px;
    height: 38px;
  }
  .contact-list svg {
    width: 22px;
    height: 22px;
    flex: none;
  }
  .service-headline {
    position: absolute;
    right: 60px;
    top: 36px;
    margin: 0;
    text-align: right;
    color: var(--teal-blue);
    font-size: 29px;
    font-weight: 700;
    line-height: 1.25;
  }
  .brand-mark {
    position: absolute;
    right: 62px;
    top: 232px;
    display: flex;
    align-items: center;
    gap: 16px;
  }
  .brand-dot {
    width: 58px;
    height: 58px;
    border-radius: 50%;
    background: var(--leaf-green-light);
    flex: none;
  }
  .brand-name {
    color: var(--ink);
    font-size: 52px;
    font-weight: 700;
    line-height: 1;
  }
  .tagline {
    position: absolute;
    right: 60px;
    bottom: 36px;
    margin: 0;
    text-align: right;
    color: var(--ink);
    font-size: 27px;
    line-height: 1.3;
  }
</style>
</head>
<body>
<div class="canvas">
  <section class="business-card">
    <svg class="card-shapes" viewBox="0 0 1000 569" aria-hidden="true">
      <circle cx="78" cy="629" r="414" fill="var(--leaf-green)" stroke="var(--arc-dark)" stroke-width="7"/>
    </svg>

    <div class="contact-block">
      <h1 class="contact-name">Maren Whitlock</h1>
      <p class="contact-role">Owner</p>
      <ul class="contact-list">
        <li>
          <svg viewBox="0 0 24 24"><path fill="currentColor" d="M6.6 10.8a15.1 15.1 0 0 0 6.6 6.6l2.2-2.2c.3-.3.7-.4 1-.2 1.1.4 2.3.6 3.6.6.6 0 1 .4 1 1V20c0 .6-.4 1-1 1A17 17 0 0 1 3 4c0-.6.4-1 1-1h3.5c.6 0 1 .4 1 1 0 1.3.2 2.5.6 3.6.1.3 0 .7-.2 1z"/></svg>
          1-855-555-NITS (6487)
        </li>
        <li>
          <svg viewBox="0 0 24 24"><rect x="2" y="5" width="20" height="14" rx="1.5" fill="currentColor"/><path d="M3 6l9 7 9-7" fill="none" stroke="var(--leaf-green)" stroke-width="1.8"/></svg>
          maren@clearnest.com
        </li>
        <li>
          <svg viewBox="0 0 24 24"><circle cx="12" cy="12" r="9" fill="none" stroke="currentColor" stroke-width="2"/><ellipse cx="12" cy="12" rx="4" ry="9" fill="none" stroke="currentColor" stroke-width="1.6"/><path d="M3 12h18" stroke="currentColor" stroke-width="1.6"/></svg>
          www.clearnest.com
        </li>
      </ul>
    </div>

    <h2 class="service-headline">All Natural In-Home<br>Lice Removal Services</h2>

    <div class="brand-mark">
      <span class="brand-dot"></span>
      <span class="brand-name">ClearNest</span>
    </div>

    <p class="tagline">Try ClearNest Today and<br>Be Lice Free Tomorrow!</p>
  </section>
</div>
</body>
</html>
```